Velvet Riot Rising Line of Sparkling Wine & Spirits

Back info: Nora Beth Quill Owner 555-318-4402 1480 E. Harlow Ave, Bldg. 2, & 3, Lodi Ca. 95871
Sparkling Wines & Memorabilia www.velvetriotrising.com
Ok I have uploaded the winning design. The color that I am after is the Fushia, Raspberry, Red, Matte Satin Matalic Finish. With a 24 Karet Gold color Foil. The Bottle is on the top row and it's the 2nd Bottle in. That is the Color that I want. This is the style of font. Make sure that you put what we're advertising. Good Luck to you all. Warmest regards, Nora
21 & up UniSex
Sparkling Wine and Memorabilia
there listed up above.....

```html
<!DOCTYPE html>
<html lang="en">
<head>
<meta charset="utf-8">
<title>Velvet Riot Rising — Business Card</title>
<link rel="stylesheet" href="https://fonts.googleapis.com/css2?family=Roboto:wght@400;500;700&display=swap">
<style>
  :root {
    --fuchsia: #c8117a;
    --raspberry: #9e1456;
    --magenta-glow: #de1a93;
    --gold: #a98437;
    --ink: #4a4a4a;
    --logo-grey: #3c3c3c;
    --paper: #ffffff;
    --backdrop: #ececec;
  }
  * { box-sizing: border-box; margin: 0; padding: 0; }
  html, body { width: 1200px; height: 1200px; overflow: hidden; }
  body {
    position: relative;
    background: var(--backdrop);
    font-family: "Roboto", Arial, sans-serif;
  }
  .card {
    position: absolute;
    width: 688px;
    height: 393px;
  }
  .card-front { left: 267px; top: 159px; background: var(--paper); }
  .card-back {
    left: 262px; top: 653px;
    background: radial-gradient(ellipse at 52% 48%, var(--magenta-glow) 0%, var(--fuchsia) 45%, var(--raspberry) 100%);
  }

  .social { position: absolute; left: 64px; top: 53px; display: flex; gap: 6px; }
  .social-dot { width: 24px; height: 24px; border-radius: 50%; background: var(--fuchsia); }

  .name {
    position: absolute; left: 64px; top: 166px;
    font-size: 26px; font-weight: 700; color: var(--fuchsia); letter-spacing: 0.2px;
  }
  .role {
    position: absolute; left: 64px; top: 190px;
    font-size: 17px; color: var(--gold);
  }
  .address {
    position: absolute; left: 64px; top: 238px;
    font-size: 16px; line-height: 21px; color: var(--ink);
  }
  .contact {
    position: absolute; left: 64px; top: 308px;
    list-style: none; font-size: 16px; line-height: 21px; color: var(--ink);
  }
  .contact li { display: flex; align-items: center; gap: 10px; }
  .contact svg { width: 14px; height: 14px; flex: none; }

  .bottle { position: absolute; }
  .bottle-front { left: 522px; top: 47px; width: 92px; height: 304px; }
  .bottle-back { left: 102px; top: 65px; width: 76px; height: 256px; }

  .brand {
    position: absolute; left: 192px; top: 162px;
    font-size: 40px; font-weight: 700; color: var(--logo-grey); letter-spacing: 0.5px;
    white-space: nowrap;
  }
  .brand-rule {
    position: absolute; left: 192px; top: 228px; width: 364px; height: 1px;
    background: rgba(255,255,255,0.35);
  }
  .tagline {
    position: absolute; left: 192px; top: 237px;
    font-size: 17px; color: #fff; letter-spacing: 2px; white-space: nowrap;
  }
  .tagline strong { font-weight: 700; }
</style>
</head>
<body>
  <section class="card card-front">
    <div class="social" aria-label="Social media">
      <span class="social-dot"></span>
      <span class="social-dot"></span>
    </div>
    <h1 class="name">NORA BETH QUILL</h1>
    <p class="role">Owner</p>
    <p class="address">E. Harlow Ave<br>Bldg. 2, &amp; 3, Lodi Ca. 95871</p>
    <ul class="contact">
      <li>
        <svg viewBox="0 0 24 24"><path fill="#c8117a" d="M6.6 10.8a15.1 15.1 0 0 0 6.6 6.6l2.2-2.2a1 1 0 0 1 1-.25 11.4 11.4 0 0 0 3.6.57 1 1 0 0 1 1 1V20a1 1 0 0 1-1 1A17 17 0 0 1 3 4a1 1 0 0 1 1-1h3.5a1 1 0 0 1 1 1c0 1.25.2 2.45.57 3.6a1 1 0 0 1-.25 1z"/></svg>
        555-318-4402 1480
      </li>
      <li>
        <svg viewBox="0 0 24 24"><circle cx="12" cy="12" r="11" fill="#c8117a"/><path fill="none" stroke="#fff" stroke-width="1.6" d="M1 12h22M12 1c3.5 3.5 3.5 18.5 0 22M12 1c-3.5 3.5-3.5 18.5 0 22"/></svg>
        www.velvetriotrising.com
      </li>
    </ul>
    <svg class="bottle bottle-front" role="img" aria-label="Illustration of a fuchsia sparkling wine bottle with gold foil neck and brand label" viewBox="0 0 92 304">
      <defs>
        <linearGradient id="bottleFront" x1="0" x2="1">
          <stop offset="0" stop-color="#b80f6e"/>
          <stop offset="0.5" stop-color="#e0208f"/>
          <stop offset="1" stop-color="#a50d62"/>
        </linearGradient>
      </defs>
      <rect width="92" height="304" rx="14" fill="url(#bottleFront)"/>
    </svg>
  </section>

  <section class="card card-back">
    <svg class="bottle bottle-back" role="img" aria-label="Illustration of a fuchsia sparkling wine bottle with gold foil neck and brand label" viewBox="0 0 76 256">
      <defs>
        <linearGradient id="bottleBack" x1="0" x2="1">
          <stop offset="0" stop-color="#b00d69"/>
          <stop offset="0.5" stop-color="#e4249a"/>
          <stop offset="1" stop-color="#a00c60"/>
        </linearGradient>
      </defs>
      <rect width="76" height="256" rx="12" fill="url(#bottleBack)"/>
    </svg>
    <h2 class="brand">Velvet Riot Rising</h2>
    <div class="brand-rule"></div>
    <p class="tagline">SPARKLING <strong>WINES &amp; MEMORABILIA</strong></p>
  </section>
</body>
</html>
```